We need a business card design for a new company located in Brampton Ontario Canada. Our goal is to promote companies to use our service as an "External Program Management " firm taking their industrial product concepts " from prototype to production." We would like to use blue and yellow as our colors. Our skills include finding suppliers for prototype parts and developing them into supplying not only prototypes but the final production parts as well for our customer base.
Industry/Entity Type
Business
Contact Information for Business Card
Derek Namsby
Sales Manager
KOLVEN Solutions Inc.
14 Pinemarsh Lane
Brampton, Ontario L7P 2K9
Canada
Phone: 905-481-2976
Fax: 905-481-2976
website: www.kolvensolutions-example.com
Email: derek@kolvensolutions-example.com
Look and feel
Each slider illustrates characteristics of the customer's brand and the style your logo design should communicate.

```html
<!DOCTYPE html>
<html lang="en">
<head>
<meta charset="utf-8">
<title>KOLVEN Solutions Inc. — Business Card</title>
<link rel="stylesheet" href="https://fonts.googleapis.com/css2?family=Open+Sans:wght@400;600;700&display=swap">
<style>
  :root {
    --backdrop: #a9aeb6;
    --card-white: #f4f4f5;
    --card-shade: #dcdcde;
    --brand-blue: #1b16d6;
    --brand-blue-deep: #1410b0;
    --accent-grey: #9a9a9d;
    --ink-light: #ffffff;
  }
  * { box-sizing: border-box; margin: 0; padding: 0; }
  html, body {
    width: 1200px; height: 866px; overflow: hidden;
    background: var(--backdrop);
    font-family: "Open Sans", Arial, sans-serif;
  }
  .stage {
    position: relative; width: 1200px; height: 866px;
    display: flex; align-items: center; justify-content: center; gap: 50px;
  }
  .card {
    position: relative; width: 525px; height: 300px; overflow: hidden;
    background: radial-gradient(ellipse at 45% 45%, var(--card-white) 30%, var(--card-shade) 100%);
    box-shadow: 0 6px 18px rgba(0,0,0,0.18);
  }
  .wordmark {
    position: absolute;
    font-weight: 700; color: var(--brand-blue-deep);
    line-height: 1.1; white-space: nowrap;
  }
  .card-front .wordmark {
    left: 0; right: 0; top: 50%; transform: translateY(-50%);
    text-align: center; font-size: 34px;
  }
  .card-back .card-shapes { position: absolute; inset: 0; }
  .card-back .wordmark {
    left: 30px; top: 130px; font-size: 23px;
  }
  .contact {
    position: absolute; right: 22px; top: 26px;
    color: var(--ink-light); text-align: right;
    font-size: 11px; line-height: 1.5;
  }
  .contact-name { font-weight: 700; font-size: 14px; }
  .contact-role { font-size: 12.5px; margin-bottom: 34px; }
  .contact-address { margin-bottom: 16px; }
  .contact-line { display: flex; align-items: center; justify-content: flex-end; gap: 5px; }
  .contact-line svg { width: 11px; height: 11px; fill: var(--ink-light); }
</style>
</head>
<body>
<main class="stage">
  <section class="card card-front" aria-label="Card front">
    <p class="wordmark">KOLVEN Solutions Inc.</p>
  </section>

  <section class="card card-back" aria-label="Card back">
    <svg class="card-shapes" viewBox="0 0 525 300" preserveAspectRatio="none" aria-hidden="true">
      <g transform="translate(-60 0)">
        <path d="M200 0 H585 V300 H360 C360 190 320 80 200 0 Z" fill="var(--brand-blue)"/>
        <path d="M178 0 C300 60 345 180 340 300 H352 C356 180 312 60 196 0 Z" fill="var(--ink-light)"/>
        <path d="M160 0 C285 60 330 180 322 300 H340 C345 180 300 60 178 0 Z" fill="var(--accent-grey)"/>
        <path d="M146 0 C272 60 318 180 308 300 H316 C326 180 280 60 158 0 Z" fill="var(--brand-blue)"/>
      </g>
    </svg>
    <p class="wordmark">KOLVEN<br>Solutions Inc.</p>
    <div class="contact">
      <p class="contact-name">Derek Namsby</p>
      <p class="contact-role">Sales Manager</p>
      <p class="contact-address">14 Pinemarsh Lane<br>Brampton L7P 2K9</p>
      <p class="contact-line">905-481-2976
        <svg viewBox="0 0 24 24"><path d="M6.6 10.8a15 15 0 0 0 6.6 6.6l2.2-2.2c.3-.3.7-.4 1-.2 1.1.4 2.3.6 3.6.6.6 0 1 .4 1 1V20c0 .6-.4 1-1 1A17 17 0 0 1 3 4c0-.6.4-1 1-1h3.5c.6 0 1 .4 1 1 0 1.3.2 2.5.6 3.6.1.3 0 .7-.2 1z"/></svg>
      </p>
      <p class="contact-line">905-481-2976
        <svg viewBox="0 0 24 24"><path d="M6 2h10v6H6zM4 9h16a2 2 0 0 1 2 2v7h-4v4H6v-4H2v-7a2 2 0 0 1 2-2zm4 7v4h8v-4z"/></svg>
      </p>
      <p class="contact-line">derek@kolvensolutions-example.com
        <svg viewBox="0 0 24 24"><path d="M2 5h20v14H2zm2 2v.5l8 5 8-5V7z"/></svg>
      </p>
      <p class="contact-line">www.kolvensolutions-example.com</p>
    </div>
  </section>
</main>
</body>
</html>
```